New Web Site Design - Tallow Ridge Communication Solutions

We are looking for a completely new web site design. Tallow Ridge Communication Solutions is a full service company providing PBX and IP/Cloud Based phone systems. We also sell and install video camera surveillance systems and provide low voltage cabling services (CAT5 and CAT3). We are looking for something professional looking. We want to be able to showcase our vendor partners as well as be able to show photos of some of the work we have done. We will also want to be able to post PDF brochures as well as make changes to the website ourselves.

Target Market(s)

Commercial

Industry/Entity Type

Communication

Coding

Coded - Design and coding required

Number of Pages Required

5+ page

Font styles to use
Sans Serif

Colors
0455a3

Requirements
Must have
• Ability to upload PDF brochures
• Professional look and feel
• Ability to upload and easily insert job photos
• Thinking it should have at least 6 pages: Main page, phone systems and services page, carrier services page, video surveillance systems and service page, low voltage cabling services page, contact us page

```html
<!DOCTYPE html>
<html lang="en">
<head>
<meta charset="utf-8">
<title>Tallow Ridge Communication Solutions</title>
<link rel="stylesheet" href="https://fonts.googleapis.com/css2?family=Open+Sans:wght@400;600;700&family=Lato:wght@400;700;900&display=swap">
<style>
:root{
  --brand:#0455a3;
  --navy:#0d3b78;
  --navy-dark:#0a2f63;
  --ink:#222;
  --muted:#555;
  --line:#e3e3e3;
  --footer:#1d1d1d;
  --footer-deep:#141414;
  --footer-text:#9a9a9a;
  --field:#2a2a2a;
  --accent-red:#d61f26;
}
*{box-sizing:border-box;margin:0;padding:0}
html,body{width:689px;height:1200px;overflow:hidden;background:#fff}
body{position:relative;font-family:"Open Sans",Arial,sans-serif;color:var(--ink)}
.abs{position:absolute}

/* header */
.site-header{left:0;top:0;width:689px;height:64px;background:#fff}
.brand{left:57px;top:17px;color:var(--navy);font-weight:400}
.brand-name{display:block;font-size:14px;line-height:15px}
.brand-tag{display:block;font-size:7.4px;line-height:10px;letter-spacing:.2px}
.partner{left:472px;top:26px;font-size:13px;font-weight:700;color:var(--accent-red);letter-spacing:.5px}
.call{left:558px;top:18px;display:flex;gap:7px;align-items:flex-start}
.call-text{font-size:9px;line-height:13px;color:var(--navy)}
.call-text b{font-weight:400;color:#222}

/* nav */
.main-nav{left:0;top:65px;width:689px;height:26px;background:var(--navy);border-top:1px solid #2a5a99}
.nav-list{position:absolute;left:57px;top:0;display:flex;list-style:none;height:26px}
.nav-list li{font-size:7px;color:#fff;line-height:26px;padding:0 15px;border-right:1px solid #2c5a94}
.nav-list li.active{background:var(--brand);padding:0 15px}
.nav-search{left:622px;top:72px}

/* hero */
.hero{left:57px;top:102px;width:575px;height:284px;background:linear-gradient(100deg,#c9d6e4 0%,#d8e2ec 45%,#b39c7d 70%,#8c7a63 100%);box-shadow:0 12px 14px -10px rgba(0,0,0,.35)}
.hero-caption{left:190px;top:334px;width:324px;height:30px;background:rgba(20,60,120,.85);color:#fff;font-size:11.5px;line-height:30px;text-align:center}
.dots{display:flex;gap:3px}
.dots i{width:5px;height:5px;border-radius:50%;background:#ccc;display:block}
.dots i.on{background:var(--navy)}
.hero-dots{left:330px;top:397px}

/* welcome */
.welcome-title{left:0;top:423px;width:689px;text-align:center;font-size:15px;font-weight:400;color:#222}
.welcome-text{left:66px;top:452px;width:556px;text-align:center;font-size:6.7px;line-height:10.2px;color:var(--muted)}

/* services */
.service-img{width:170px;height:111px;box-shadow:0 6px 6px -5px rgba(0,0,0,.4)}
.svc-cloud{left:64px;top:535px;background:linear-gradient(180deg,#c9ccd2 0%,#6e8fbf 40%,#2f5c9e 100%)}
.svc-camera{left:257px;top:535px;background:linear-gradient(180deg,#8c8a86 0%,#c9c6c0 45%,#a9a39a 100%)}
.svc-cabling{left:450px;top:535px;background:linear-gradient(180deg,#7a8d96 0%,#9fb3ba 50%,#7f959c 100%)}
.service-caption{width:180px;text-align:center;font-size:8.6px;line-height:13.5px;color:#333;top:660px}

/* testimonials */
.section-title{left:57px;top:713px;font-size:14.5px;font-weight:400;color:#111}
.arrows{left:612px;top:716px;display:flex;gap:2px}
.testimonial{width:185px;height:60px;top:765px}
.avatar{position:absolute;left:0;top:0;width:53px;height:53px;border-radius:50%;background:linear-gradient(160deg,#d9d4cc,#8f8579);border:2px solid #eee}
.t-name{position:absolute;left:63px;top:3px;font-size:7.5px;font-weight:600;color:#222}
.t-text{position:absolute;left:63px;top:16px;width:122px;font-size:5.6px;line-height:8.4px;font-weight:600;color:#555}
.t-more{position:absolute;left:135px;top:50px;font-size:5.6px;font-weight:600;color:#333;display:flex;gap:4px;align-items:center}
.t-dots{left:332px;top:843px}

/* cta */
.cta{left:0;top:884px;width:689px;height:57px;background:var(--navy)}
.cta-text{left:113px;top:905px;font-size:10.5px;color:#fff}
.cta-btn{left:475px;top:901px;width:99px;height:24px;background:var(--brand);color:#fff;font-size:8px;line-height:24px;text-align:center;text-transform:uppercase}

/* footer */
.site-footer{left:0;top:941px;width:689px;height:223px;background:var(--footer)}
.f-col-line{top:979px;width:1px;height:148px;background:#2c2c2c}
.f-title{top:981px;font-family:"Lato",Arial,sans-serif;font-weight:900;font-size:9.5px;letter-spacing:1px;color:#fff}
.f-links{left:59px;top:1015px;list-style:none}
.f-links li{font-size:6.4px;color:var(--footer-text);line-height:17.6px;display:flex;align-items:center;gap:9px}
.f-links li::before{content:"";width:4px;height:4px;border-radius:50%;background:#8a8a8a}
.f-contact{left:251px;top:1017px;font-size:6.4px;line-height:9.5px;color:var(--footer-text)}
.f-row{display:flex;gap:9px;margin-bottom:8px;align-items:flex-start}
.f-field{left:451px;width:182px;height:20px;background:var(--field);border:1px solid #333;font-size:6.4px;color:#bbb;line-height:19px;padding-left:7px}
.f-field svg{position:absolute;right:8px;top:6px}
.f-area{left:451px;top:1060px;width:182px;height:42px;background:var(--field);border:1px solid #333}
.f-send{left:451px;top:1109px;width:182px;height:20px;background:var(--navy);color:#fff;font-family:"Lato",Arial,sans-serif;font-weight:900;font-size:7.5px;letter-spacing:1px;line-height:20px;text-align:center}
.bottom-bar{left:0;top:1164px;width:689px;height:36px;background:var(--footer-deep);border-top:1px solid #2a2a2a}
.copyright{left:58px;top:1179px;font-size:6.4px;color:#999}
.social{left:530px;top:1180px;display:flex;gap:7px}
.social i{display:block;width:6px;height:6px;border-radius:50%;background:#ddd}
</style>
</head>
<body>

<header class="site-header abs">
  <div class="brand abs">
    <span class="brand-name">Tallow Ridge</span>
    <span class="brand-tag">COMMUNICATION SOLUTIONS</span>
  </div>
  <div class="partner abs">NORVANE</div>
  <div class="call abs">
    <svg width="12" height="16" viewBox="0 0 12 16"><path d="M3 1l3 3-2 2c1 2 2 4 4 5l2-2 2 3-2 2C5 14 1 8 1 3z" fill="#0d3b78"/></svg>
    <div class="call-text">Call Us<br><b>+48 210 5577</b></div>
  </div>
</header>

<nav class="main-nav abs">
  <ul class="nav-list">
    <li class="active">Home</li>
    <li>Phone systems</li>
    <li>Carrier</li>
    <li>Video Surveillance</li>
    <li>Low voltage cabling</li>
    <li>Contact us</li>
  </ul>
</nav>
<svg class="nav-search abs" width="11" height="11" viewBox="0 0 11 11"><circle cx="4.5" cy="4.5" r="3.3" fill="none" stroke="#fff" stroke-width="1.4"/><path d="M7 7l3 3" stroke="#fff" stroke-width="1.5"/></svg>

<div class="hero abs" role="img" aria-label="Technician in a hard hat installing a camera on a building wall under a blue sky"></div>
<div class="hero-caption abs">We provide PBX and IP/Cloud Based phone systems</div>
<div class="dots hero-dots abs"><i class="on"></i><i></i><i></i><i></i></div>

<h1 class="welcome-title abs">Welcome To Our Site</h1>
<p class="welcome-text abs">Lorem ipsum dolor sit amet, consectetur adipiscing elit. Nunc nec luctus urna, ut malesuada tortor. Morbi ac aliquet enim, eu interdum est. Nulla sed mi nec libero pulvinar bibendum vel vitae ligula. Praesent condimentum sagittis nunc quis pharetra. Nulla aliquet varius leo, nec facilisis arcu vulputate rutrum. Donec tempus laoreet tortor id elementum. Nam sagittis est nibh, ac hendrerit lectus iaculis eleifend. Vivamus at porta felis. Donec id nisl et lorem mattis mattis in et libero. Sed ut felis vitae velit facilisis molestie dictum id eros. Aliquam erat volutpat. Suspendisse eget vulputate magna. Maecenas eu blandit ligula, tincidunt commodo nisl. Fusce ut risus fringilla, vehicula risus vitae, aliquet magna.</p>

<div class="service-img svc-cloud abs" role="img" aria-label="Hand under a cloud connected to phone, tablet, laptop, desktop and server"></div>
<div class="service-img svc-camera abs" role="img" aria-label="Ceiling mounted dome security camera in an empty room"></div>
<div class="service-img svc-cabling abs" role="img" aria-label="Network cables running along a ceiling tray with labels"></div>
<p class="service-caption abs" style="left:59px">PBX and IP/Cloud Based phone systems</p>
<p class="service-caption abs" style="left:252px">Sell and install video camera surveillance systems</p>
<p class="service-caption abs" style="left:445px">Low voltage cabling services (CAT5 and CAT3)</p>

<h2 class="section-title abs">Client Testimonials</h2>
<div class="arrows abs">
  <svg width="9" height="12" viewBox="0 0 9 12"><path d="M7 1L2 6l5 5" fill="none" stroke="#0d3b78" stroke-width="2"/></svg>
  <svg width="9" height="12" viewBox="0 0 9 12"><path d="M2 1l5 5-5 5" fill="none" stroke="#bbb" stroke-width="1.5"/></svg>
</div>

<div class="testimonial abs" style="left:57px">
  <div class="avatar" role="img" aria-label="Client portrait"></div>
  <div class="t-name">JHON DOE</div>
  <p class="t-text">Donec sed lorem tincidunt, viverra diam vel, auctor dolor. Donec urna magna, auctor porttitor</p>
  <div class="t-more">Read More <svg width="7" height="7" viewBox="0 0 7 7"><circle cx="3.5" cy="3.5" r="3" fill="none" stroke="#666" stroke-width=".7"/><path d="M2.5 2l1.5 1.5-1.5 1.5" fill="none" stroke="#666" stroke-width=".7"/></svg></div>
</div>
<div class="testimonial abs" style="left:254px">
  <div class="avatar" role="img" aria-label="Client portrait"></div>
  <div class="t-name">JHON DOE</div>
  <p class="t-text">Donec sed lorem tincidunt, viverra diam vel, auctor dolor. Donec urna magna, auctor porttitor</p>
  <div class="t-more">Read More <svg width="7" height="7" viewBox="0 0 7 7"><circle cx="3.5" cy="3.5" r="3" fill="none" stroke="#666" stroke-width=".7"/><path d="M2.5 2l1.5 1.5-1.5 1.5" fill="none" stroke="#666" stroke-width=".7"/></svg></div>
</div>
<div class="testimonial abs" style="left:449px">
  <div class="avatar" role="img" aria-label="Client portrait"></div>
  <div class="t-name">JHON DOE</div>
  <p class="t-text">Donec sed lorem tincidunt, viverra diam vel, auctor dolor. Donec urna magna, auctor porttitor</p>
  <div class="t-more">Read More <svg width="7" height="7" viewBox="0 0 7 7"><circle cx="3.5" cy="3.5" r="3" fill="none" stroke="#666" stroke-width=".7"/><path d="M2.5 2l1.5 1.5-1.5 1.5" fill="none" stroke="#666" stroke-width=".7"/></svg></div>
</div>
<div class="dots t-dots abs"><i class="on" style="width:4px;height:4px"></i><i style="width:4px;height:4px"></i><i style="width:4px;height:4px"></i><i style="width:4px;height:4px"></i></div>

<section class="cta abs"></section>
<p class="cta-text abs">Aenean ut justo diam. Vivamus ultricies, justo ut vestibulum sollicitudin</p>
<div class="cta-btn abs">Contact now</div>

<footer class="site-footer abs"></footer>
<div class="f-col-line abs" style="left:191px"></div>
<div class="f-col-line abs" style="left:388px"></div>

<h3 class="f-title abs" style="left:57px">QUICK LINKS</h3>
<ul class="f-links abs">
  <li>Home</li><li>Phone systems</li><li>Carrier</li><li>Video Surveillance</li><li>Low voltage cabling</li><li>Contact us</li>
</ul>

<h3 class="f-title abs" style="left:253px">CONTACT</h3>
<div class="f-contact abs">
  <div class="f-row"><svg width="7" height="9" viewBox="0 0 7 9"><path d="M3.5 0A3 3 0 0 0 .5 3c0 2.5 3 6 3 6s3-3.5 3-6a3 3 0 0 0-3-3z" fill="#aaa"/><circle cx="3.5" cy="3" r="1.1" fill="#1d1d1d"/></svg><span>2840 Linden Crest Rd.<br>Millbrook, KS 66031</span></div>
  <div class="f-row"><svg width="7" height="8" viewBox="0 0 12 16"><path d="M3 1l3 3-2 2c1 2 2 4 4 5l2-2 2 3-2 2C5 14 1 8 1 3z" fill="#aaa"/></svg><span>Commercial: (555)204-7130</span></div>
  <div class="f-row"><svg width="8" height="8" viewBox="0 0 8 8"><rect x="0" y="2" width="8" height="6" fill="#aaa"/><rect x="2" y="0" width="4" height="3" fill="#aaa"/><rect x="2" y="4" width="4" height="1" fill="#1d1d1d"/></svg><span>Fax: (555)204-7131</span></div>
</div>

<h3 class="f-title abs" style="left:450px">QUICK CONTACT US</h3>
<div class="f-field abs" style="top:1011px">Name<svg width="7" height="7" viewBox="0 0 7 7"><circle cx="3.5" cy="2" r="1.6" fill="#bbb"/><path d="M0.5 7a3 3 0 0 1 6 0z" fill="#bbb"/></svg></div>
<div class="f-field abs" style="top:1035px">you@example.com<svg width="7" height="6" viewBox="0 0 7 6"><rect x=".5" y=".5" width="6" height="5" fill="none" stroke="#bbb"/><path d="M.5 .5l3 2.5 3-2.5" fill="none" stroke="#bbb"/></svg></div>
<div class="f-area abs"></div>
<div class="f-send abs">SEND IT NOW</div>

<div class="bottom-bar abs"></div>
<p class="copyright abs">Copyright 2015 tallowridge. All Rights Reserved</p>
<div class="social abs"><i></i><i></i><i></i><i></i><i></i><i></i><i></i><i></i></div>

</body>
</html>
```